Book cover for book about Climate Change

Looking for a clean, bold, and attractive cover for a mass-market paperback (5.5"x 8.5") about solving the climate change problem. Title is either "Where the Rivers Meet” or A Harbor Made of Glass” (your choice), subtitle is "A practical field guide to mending the weather — so that the young ones after us inherit steady seasons and open skies," author is Lorne Whitcombe. Thinking that it *might* feature an image of Earth (or a portion thereof) and its very thin layer of atmosphere -- but STRONGLY encourage other ideas too!

Requirements
Nice to have
• Keep it positive — NOT scary doom-and-gloom

```html
<!DOCTYPE html>
<html lang="en">
<head>
<meta charset="utf-8">
<title>Where the Rivers Meet — Lorne Whitcombe</title>
<link rel="stylesheet" href="https://fonts.googleapis.com/css2?family=Open+Sans:wght@300;400;800&display=swap">
<style>
  :root {
    --sky-top: #1f3556;
    --sky-mid: #0d1a2c;
    --sky-bottom: #070a10;
    --planet-light: #cfe6ff;
    --planet-mid: #3f7fc4;
    --planet-deep: #0c2340;
    --glow: #4aa3ff;
    --skin-tone: #b48c74;
    --ink: #ffffff;
  }
  html, body {
    margin: 0;
    padding: 0;
    overflow: hidden;
    background: var(--sky-bottom);
  }
  .cover {
    position: relative;
    width: 840px;
    height: 1200px;
    overflow: hidden;
    background: linear-gradient(180deg, var(--sky-top) 0%, var(--sky-mid) 45%, var(--sky-bottom) 100%);
    font-family: "Open Sans", Arial, sans-serif;
    color: var(--ink);
  }
  .artwork {
    position: absolute;
    inset: 0;
  }
  .author {
    position: absolute;
    top: 30px;
    left: 0;
    width: 100%;
    text-align: center;
    font-weight: 400;
    font-size: 35px;
    line-height: 46px;
    letter-spacing: 0.11em;
    padding-left: 0.11em;
    box-sizing: border-box;
    margin: 0;
  }
  .title {
    position: absolute;
    top: 560px;
    left: 0;
    width: 100%;
    margin: 0;
    text-align: center;
    font-weight: 400;
  }
  .title-lead {
    display: block;
    font-size: 50px;
    font-weight: 400;
    line-height: 60px;
  }
  .title-middle {
    display: block;
    font-size: 66px;
    font-weight: 300;
    letter-spacing: 0.2em;
    padding-left: 0.2em;
    line-height: 86px;
  }
  .title-main {
    display: block;
    font-size: 200px;
    font-weight: 800;
    line-height: 180px;
    letter-spacing: -0.02em;
    text-shadow: 0 0 40px rgba(74, 163, 255, 0.55);
  }
  .subtitle {
    position: absolute;
    top: 940px;
    left: 70px;
    width: 700px;
    margin: 0;
    text-align: center;
    font-size: 22px;
    line-height: 30px;
    font-weight: 400;
  }
</style>
</head>
<body>
<main class="cover">
  <svg class="artwork" width="840" height="1200" viewBox="0 0 840 1200">
    <defs>
      <radialGradient id="planet-fill" cx="0.7" cy="0.3" r="0.85">
        <stop offset="0" stop-color="var(--planet-light)"/>
        <stop offset="0.35" stop-color="var(--planet-mid)"/>
        <stop offset="0.75" stop-color="var(--planet-deep)"/>
        <stop offset="1" stop-color="#050b16"/>
      </radialGradient>
      <radialGradient id="halo" cx="0.5" cy="0.5" r="0.5">
        <stop offset="0.82" stop-color="var(--glow)" stop-opacity="0.55"/>
        <stop offset="1" stop-color="var(--glow)" stop-opacity="0"/>
      </radialGradient>
      <radialGradient id="title-glow" cx="0.5" cy="0.5" r="0.5">
        <stop offset="0" stop-color="#1f4f86" stop-opacity="0.7"/>
        <stop offset="1" stop-color="#1f4f86" stop-opacity="0"/>
      </radialGradient>
      <radialGradient id="side-tone" cx="0.5" cy="0.5" r="0.5">
        <stop offset="0" stop-color="var(--skin-tone)" stop-opacity="0.55"/>
        <stop offset="1" stop-color="var(--skin-tone)" stop-opacity="0"/>
      </radialGradient>
    </defs>

    <ellipse cx="420" cy="810" rx="420" ry="200" fill="url(#title-glow)"/>

    <g role="img" aria-label="Photograph of planet Earth glowing blue against space">
      <circle cx="435" cy="360" r="310" fill="url(#halo)"/>
      <circle cx="435" cy="360" r="278" fill="url(#planet-fill)"/>
    </g>

    <rect role="img" aria-label="Photograph of a left hand cupping the planet from the side"
          x="-120" y="60" width="340" height="440" fill="url(#side-tone)"/>
    <rect role="img" aria-label="Photograph of a right hand cupping the planet from the side"
          x="620" y="60" width="340" height="440" fill="url(#side-tone)"/>
  </svg>

  <p class="author">LORNE WHITCOMBE</p>

  <h1 class="title">
    <span class="title-lead">Where the</span>
    <span class="title-middle">RIVERS</span>
    <span class="title-main">MEET</span>
  </h1>

  <p class="subtitle">A practical field guide to mending the weather — so that the young ones after us inherit steady seasons and open skies</p>
</main>
</body>
</html>
```